KRV Photography Business Card Design

I would like a business card designed in the shape of a camera.
Would like to see various camera designs. Would like to see what the card looks like in different colors. Would like to see which logo looks better on the various camera designs so please show me some with the white logo and some with the black logo. If you need a different file formats please let me know.
Project Deadline Extended Reason: My grandfather passed away and dealing with funeral plans so need to extend deadline. Added Tuesday, March 1, 2016
Project Deadline Extended
Reason: I just got back from out of town. My grandfather's passing was the primary focus for me these past few weeks and the funeral is over so now I will concentrate on picking my business card design. I really appreciate each designer who has taken the time to submit a design. Your effort has not gone unnoticed. I look forward to seeing more amazing designs.
Business
Contact Information for Business Card
Dorine
555-418-2706
https://www.facebook.com/krvphotographyfreelance/
MonaDorine@krv-photography.example

```html
<!DOCTYPE html>
<html lang="en">
<head>
<meta charset="utf-8">
<title>KRV Photography Business Card</title>
<link rel="stylesheet" href="https://fonts.googleapis.com/css2?family=Cinzel:wght@400&family=Open+Sans:wght@400;700&display=swap">
<style>
  :root {
    --page: #bdbec0;
    --card: #000000;
    --gold: #d4a43a;
    --gold-light: #f2d47a;
    --amber: #cf8a2c;
    --white: #ffffff;
    --faint: #2a1a08;
  }
  * { margin: 0; padding: 0; box-sizing: border-box; }
  html, body { width: 1200px; height: 737px; overflow: hidden; background: var(--page); }
  .stage { position: relative; width: 1200px; height: 737px; }
  .card { position: absolute; top: 233px; width: 425px; height: 271px; }
  .card--amber { left: 153px; --accent: var(--amber); }
  .card--white { left: 607px; --accent: var(--white); }
  .card__shape { position: absolute; inset: 0; }
  .brand { position: absolute; left: 30px; top: 91px; width: 190px; text-align: center; }
  .brand__dot {
    display: block; width: 56px; height: 56px; margin: 0 auto 10px;
    border-radius: 50%;
    background: radial-gradient(circle at 40% 35%, var(--gold-light), var(--gold) 70%);
  }
  .brand__name {
    font-family: "Cinzel", serif; font-size: 17px; color: var(--gold);
    white-space: nowrap; letter-spacing: 0.2px;
  }
  .divider {
    position: absolute; left: 225px; top: 115px; width: 1.5px; height: 80px;
    background: linear-gradient(to bottom, transparent, var(--gold-light) 40%, var(--gold) 70%, transparent);
  }
  .contact { position: absolute; left: 239px; top: 126px; font-family: "Open Sans", sans-serif; color: var(--accent); }
  .contact__name { font-weight: 700; font-size: 17.5px; letter-spacing: 1.4px; line-height: 22px; }
  .contact__line { display: flex; align-items: center; gap: 9px; font-size: 10.5px; letter-spacing: 0.6px; line-height: 13px; }
  .contact__line:first-of-type { margin-top: 5px; }
  .contact__line svg { width: 8px; height: 8px; flex: none; }
</style>
</head>
<body>
<main class="stage">
  <section class="card card--amber" aria-label="Business card, amber contact text">
    <svg class="card__shape" viewBox="0 0 425 271" aria-hidden="true">
      <defs>
        <radialGradient id="faint-a" cx="0.4" cy="0.4" r="0.7">
          <stop offset="0" stop-color="#3a2410" stop-opacity="0.55"/>
          <stop offset="1" stop-color="#1a1005" stop-opacity="0.5"/>
        </radialGradient>
      </defs>
      <rect x="56" y="11" width="49" height="12" rx="4" fill="var(--card)"/>
      <rect x="299" y="0" width="82" height="24" rx="6" fill="var(--card)"/>
      <rect x="0" y="16" width="425" height="255" rx="16" fill="var(--card)"/>
      <circle cx="221" cy="143" r="124" fill="url(#faint-a)"/>
    </svg>
    <div class="brand"><span class="brand__dot"></span><span class="brand__name">KRV PHOTOGRAPHY</span></div>
    <div class="divider"></div>
    <div class="contact">
      <p class="contact__name">THEO VARGA</p>
      <p class="contact__line"><svg viewBox="0 0 10 10"><path d="M2 0.5 L4 2.8 L3 4 Q4.5 6 6 7 L7.2 6 L9.5 8 L8 9.5 Q3 9 0.5 2 Z" fill="currentColor"/></svg>+330 2460-1594</p>
      <p class="contact__line"><svg viewBox="0 0 10 10"><rect x="0.6" y="1.6" width="8.8" height="6.8" fill="none" stroke="currentColor" stroke-width="1.1"/><path d="M0.6 1.8 L5 5.5 L9.4 1.8" fill="none" stroke="currentColor" stroke-width="1.1"/></svg>theo@vargamail.example</p>
    </div>
  </section>

  <section class="card card--white" aria-label="Business card, white contact text">
    <svg class="card__shape" viewBox="0 0 425 271" aria-hidden="true">
      <defs>
        <radialGradient id="faint-b" cx="0.4" cy="0.4" r="0.7">
          <stop offset="0" stop-color="#3a2410" stop-opacity="0.55"/>
          <stop offset="1" stop-color="#1a1005" stop-opacity="0.5"/>
        </radialGradient>
      </defs>
      <rect x="56" y="11" width="49" height="12" rx="4" fill="var(--card)"/>
      <rect x="299" y="0" width="82" height="24" rx="6" fill="var(--card)"/>
      <rect x="0" y="16" width="425" height="255" rx="16" fill="var(--card)"/>
      <circle cx="221" cy="143" r="124" fill="url(#faint-b)"/>
    </svg>
    <div class="brand"><span class="brand__dot"></span><span class="brand__name">KRV PHOTOGRAPHY</span></div>
    <div class="divider"></div>
    <div class="contact">
      <p class="contact__name">THEO VARGA</p>
      <p class="contact__line"><svg viewBox="0 0 10 10"><path d="M2 0.5 L4 2.8 L3 4 Q4.5 6 6 7 L7.2 6 L9.5 8 L8 9.5 Q3 9 0.5 2 Z" fill="currentColor"/></svg>+330 2460-1594</p>
      <p class="contact__line"><svg viewBox="0 0 10 10"><rect x="0.6" y="1.6" width="8.8" height="6.8" fill="none" stroke="currentColor" stroke-width="1.1"/><path d="M0.6 1.8 L5 5.5 L9.4 1.8" fill="none" stroke="currentColor" stroke-width="1.1"/></svg>theo@vargamail.example</p>
    </div>
  </section>
</main>
</body>
</html>
```